website redesign - tallowgrange.com.au

need to redesign our website. we are proud of our current website but market feedback suggests that we have to tone down our quirkiness and make it look more professional to target the million dollar market.
right now we appeal to the younger generation so we have to meet somewhere in the middle.
we want to still retain our same flavour and style but need to also look a bit more professional. we need to evolve our brand to a more grown up look.
examples of standard websites include copperleaf property, wren property, lodging ledger, pellings onward, dunmore

```html
<!DOCTYPE html>
<html lang="en">
<head>
<meta charset="utf-8">
<title>Tallowgrange Realty — Our Team</title>
<link href="https://fonts.googleapis.com/css2?family=Jost:wght@400;500;600&family=Caveat:wght@500&display=swap" rel="stylesheet">
<style>
:root{
  --orange:#f04e0f;
  --navy:#13274b;
  --ink:#1d2433;
  --muted:#7d8594;
  --line:#e4e7ec;
  --band:#f7f8fa;
  --white:#ffffff;
}
*{box-sizing:border-box;margin:0;padding:0}
html,body{width:755px;height:1200px;overflow:hidden;background:var(--white);font-family:'Jost',sans-serif;color:var(--ink)}
.page{position:relative;width:755px;height:1200px}
.abs{position:absolute}
.brand{font-family:'Jost',sans-serif;font-weight:500;font-size:10px;letter-spacing:.8px;color:#5c6270;display:flex;align-items:center;gap:5px}
.brand-mark{width:7px;height:7px;background:var(--orange)}
.site-header{left:0;top:0;width:755px;height:57px;border-bottom:1px solid #f0f1f3}
.header-cta{left:573px;top:14px;width:80px;height:26px;border:1px solid var(--orange);color:var(--orange);font-size:8px;display:flex;align-items:center;justify-content:center;border-radius:1px}
.menu-btn{left:678px;top:16px;width:22px;height:22px;border-radius:50%;background:var(--orange);display:flex;align-items:center;justify-content:center}
.team-band{left:0;top:113px;width:755px;height:222px;background:var(--band)}
.team-title{left:80px;top:158px;font-size:32px;font-weight:500;color:var(--navy);letter-spacing:-.3px}
.script{font-family:'Caveat',cursive;color:var(--orange);font-size:14px}
.card{width:165px;height:195px;background:var(--white);border:1px solid var(--line);border-radius:3px;overflow:hidden}
.card.featured{box-shadow:0 4px 14px rgba(20,30,50,.09)}
.card-head{height:50px;padding:11px 19px 0}
.card-role{font-size:8px;color:var(--muted)}
.card-name{font-size:12.5px;color:var(--navy);margin-top:1px}
.card-photo{height:145px}
.card.featured .card-photo{height:113px}
.card-foot{height:32px;display:flex;align-items:center;justify-content:space-between;padding:0 22px;font-size:7.5px;color:var(--ink)}
.believe{left:0;top:690px;width:755px;height:238px;background:var(--band)}
.believe-title{left:72px;top:757px;font-size:21px;font-weight:500;color:var(--navy)}
.believe-copy{left:72px;top:789px;width:330px;font-size:10.2px;line-height:15.8px;color:var(--muted)}
.believe-cta{left:72px;top:853px;width:101px;height:34px;background:var(--orange);color:var(--white);font-size:9px;display:flex;align-items:center;justify-content:center}
.believe-photo{left:427px;top:690px;width:328px;height:238px;background:linear-gradient(135deg,#b89a7c 0%,#8a7a6c 40%,#3d5d82 75%,#2f4f77 100%)}
.play{left:572px;top:792px;width:31px;height:31px;border-radius:50%;background:var(--orange);display:flex;align-items:center;justify-content:center}
.site-footer{left:0;top:943px;width:755px;height:257px;background:var(--band)}
.foot-h{font-size:7.8px;font-weight:500;color:var(--navy)}
.foot-link{font-size:7.6px;color:var(--ink)}
.phone-pill{left:393px;top:1060px;width:120px;height:25px;background:var(--white);border-radius:4px;display:flex;align-items:center;gap:5px;padding-left:9px;box-shadow:0 2px 8px rgba(20,30,50,.05)}
.phone-dot{width:9px;height:9px;border-radius:50%;background:#21c1d6}
.social{width:28px;height:28px;border-radius:50%;background:var(--navy);display:flex;align-items:center;justify-content:center}
.social.active{background:var(--orange);box-shadow:0 3px 8px rgba(240,78,15,.3)}
.social-glyph{width:9px;height:9px;border-radius:50%;background:var(--white)}
.copyright{left:0;top:1160px;width:755px;text-align:center;font-size:6.5px;color:var(--navy)}
.legal{left:0;top:1176px;width:755px;text-align:center;font-size:4.6px;color:var(--navy)}
</style>
</head>
<body>
<div class="page">

  <header class="site-header abs">
    <div class="brand abs" style="left:55px;top:23px"><span class="brand-mark"></span>TALLOWGRANGE REALTY</div>
    <a class="header-cta abs">Contact us</a>
    <div class="menu-btn abs">
      <svg width="9" height="7" viewBox="0 0 9 7"><path d="M0 .5H9M0 3.5H9M0 6.5H9" stroke="#fff" stroke-width=".8"/></svg>
    </div>
  </header>

  <section>
    <div class="team-band abs"></div>
    <h1 class="team-title abs">Our Team</h1>
    <div class="script abs" style="left:559px;top:152px">#TeamTallow</div>
    <svg class="abs" style="left:532px;top:172px" width="24" height="30" viewBox="0 0 24 30">
      <path d="M22 2C12 2 6 10 7 26" fill="none" stroke="#f04e0f" stroke-width="1"/>
      <path d="M4 23L7 28L10 23" fill="none" stroke="#f04e0f" stroke-width="1"/>
    </svg>

    <article class="card featured abs" style="left:81px;top:228px">
      <div class="card-head"><div class="card-role">Ceo</div><div class="card-name">Rowan Ashby</div></div>
      <div class="card-photo" role="img" aria-label="Portrait of the CEO seated outdoors in a navy suit" style="background:linear-gradient(120deg,#9a7a66,#3f5f86 45%,#6f9a58 80%,#a8c98a)"></div>
      <div class="card-foot"><span>Read bio</span>
        <svg width="12" height="6" viewBox="0 0 12 6"><path d="M0 3H11M8 .5L11 3L8 5.5" fill="none" stroke="#1d2433" stroke-width=".8"/></svg>
      </div>
    </article>
    <article class="card abs" style="left:296px;top:228px">
      <div class="card-head"><div class="card-role">Coo</div><div class="card-name">Lucia Ferrand</div></div>
      <div class="card-photo" role="img" aria-label="Portrait of the COO against a grey office backdrop" style="background:linear-gradient(160deg,#9fb0b3,#7a7068 55%,#d7d6d2)"></div>
    </article>
    <article class="card abs" style="left:511px;top:228px">
      <div class="card-head"><div class="card-role">Manger</div><div class="card-name">Hanna Corley</div></div>
      <div class="card-photo" role="img" aria-label="Portrait of the manager beside an orange wall and window" style="background:linear-gradient(90deg,#f2913f,#d9762e 40%,#7d7570 65%,#cfc6bc)"></div>
    </article>

    <article class="card abs" style="left:81px;top:453px">
      <div class="card-head"><div class="card-role">Designer</div><div class="card-name">Elliot Marsh</div></div>
      <div class="card-photo" role="img" aria-label="Designer sketching on a pinboard of notes" style="background:linear-gradient(110deg,#d9dde2,#eef0f2 45%,#b9a99c 75%,#c2c5ca)"></div>
    </article>
    <article class="card abs" style="left:296px;top:453px">
      <div class="card-head"><div class="card-role">Super Agent</div><div class="card-name">Dana Whitlow</div></div>
      <div class="card-photo" role="img" aria-label="Agent working at a desk with monitors in a dim office" style="background:linear-gradient(140deg,#1c3440,#0e1d26 50%,#5a3a30 85%,#23313a)"></div>
    </article>
    <article class="card abs" style="left:511px;top:453px">
      <div class="card-head"><div class="card-role">Agent</div><div class="card-name">Owen Pratley</div></div>
      <div class="card-photo" role="img" aria-label="Portrait of the agent in striped window light" style="background:linear-gradient(135deg,#5e5650,#8c7f74 45%,#3b3632 80%)"></div>
    </article>
  </section>

  <section>
    <div class="believe abs"></div>
    <div class="script abs" style="left:72px;top:735px">#TeamTallow</div>
    <h2 class="believe-title abs">Here's What We Believe</h2>
    <p class="believe-copy abs">We make every effort to inject a little personality into an industry that’s far too up itself. You can trust us with your most valuable investments. In return, we give you our commitment to always do the right thing by you.</p>
    <a class="believe-cta abs">Contact us</a>
    <div class="believe-photo abs" role="img" aria-label="Team meeting in a brick-walled office with a whiteboard"></div>
    <div class="play abs">
      <svg width="10" height="11" viewBox="0 0 10 11"><path d="M1 0L10 5.5L1 11Z" fill="#fff"/></svg>
    </div>
  </section>

  <footer class="site-footer abs">
    <div class="brand abs" style="left:57px;top:52px"><span class="brand-mark"></span>TALLOWGRANGE REALTY</div>

    <div class="foot-h abs" style="left:236px;top:52px">Navigation</div>
    <div class="foot-link abs" style="left:236px;top:74px">Home</div>
    <div class="foot-link abs" style="left:236px;top:92px">About us</div>
    <div class="foot-link abs" style="left:236px;top:111px">Properties</div>
    <div class="foot-link abs" style="left:236px;top:129px">Contact</div>

    <div class="foot-h abs" style="left:314px;top:52px">Product</div>
    <div class="foot-link abs" style="left:314px;top:73px">Property</div>
    <div class="foot-link abs" style="left:314px;top:92px">Stayvale</div>
    <div class="foot-link abs" style="left:314px;top:111px">Finance</div>
    <div class="foot-link abs" style="left:314px;top:129px">Reviews</div>

    <div class="foot-h abs" style="left:393px;top:52px">Adress</div>
    <div class="foot-link abs" style="left:393px;top:73px">4/21 Fernleaf Rd, Kelmore QLD 4099</div>
    <div class="foot-link abs" style="left:393px;top:90px">hello@tallowgrange.com.au</div>

    <div class="foot-h abs" style="left:564px;top:52px">Social Media</div>
    <div class="social abs" style="left:564px;top:82px" aria-label="Social link one"><span class="social-glyph"></span></div>
    <div class="social active abs" style="left:602px;top:82px" aria-label="Social link two"><span class="social-glyph"></span></div>
    <div class="social abs" style="left:638px;top:82px" aria-label="Social link three"><span class="social-glyph"></span></div>
  </footer>

  <div class="phone-pill abs">
    <span class="phone-dot"></span>
    <span style="font-size:4px;color:var(--navy)">Call us on</span>
    <span style="font-size:6.5px;font-weight:600;letter-spacing:1.6px;color:var(--navy)">0412-555-208</span>
  </div>

  <div class="copyright abs">© &nbsp;Tallowgrange Realty Company - All Rights Reserved</div>
  <div class="legal abs">Terms &amp; Conditions | Privacy Policy | Compliance Policy | Contact Us</div>

</div>
</body>
</html>
```